Veltrano.co - Polar Expeditions Specialists

We need a modern, visually striking business card for Veltrano.co, a company specialized in selling expedition cruises to the most remote regions on Earth, with a focus on the Arctic and Antarctica. The design should instantly communicate that the cardholder is an expert in polar travel. Use clean, premium aesthetics with cool tones like icy blue and white, possibly incorporating polar imagery (ice, glaciers, penguins, etc.)

Attached the logo

Contact Information for Business Card

Feels high-end and trustworthy.. Visually memorable — encourages people to keep it

Colors
0054AA
0677BA
7BADD7
CADEEF
E8F1F8

Requirements
Must have
• ice, glaciers, penguins, montains
Nice to have
• modern, transparente,

```html
<!DOCTYPE html>
<html lang="en">
<head>
<meta charset="utf-8">
<title>Veltrano.co – Business Card</title>
<link href="https://fonts.googleapis.com/css2?family=Poppins:wght@400;500;600&family=Roboto:wght@400;500;700&display=swap" rel="stylesheet">
<style>
  :root {
    --backdrop: #3a3a3a;
    --card-blue: #3473b5;
    --deep-blue: #1d3f8f;
    --ice-blue: #cadeef;
    --frost: #e8f1f8;
    --white: #ffffff;
    --divider: #5a5f66;
  }
  * { box-sizing: border-box; margin: 0; padding: 0; }
  html, body { width: 1200px; height: 689px; overflow: hidden; }
  body {
    background: var(--backdrop);
    display: flex;
    align-items: center;
    justify-content: center;
    gap: 40px;
    font-family: "Poppins", sans-serif;
  }
  .card {
    width: 520px;
    height: 300px;
    border-radius: 22px;
    overflow: hidden;
    position: relative;
  }
  /* Front */
  .card-front {
    background: var(--card-blue);
    display: flex;
    align-items: center;
    justify-content: center;
  }
  .brand { display: flex; align-items: center; gap: 16px; }
  .brand-mark {
    flex: none;
    width: 72px; height: 72px; border-radius: 50%;
    background: var(--deep-blue);
  }
  .brand-text { display: flex; flex-direction: column; }
  .brand-name {
    font-weight: 600;
    font-size: 56px;
    line-height: 1;
    color: var(--ice-blue);
    white-space: nowrap;
  }
  .brand-tagline {
    font-size: 16px;
    color: var(--ice-blue);
    margin-top: 8px;
    letter-spacing: 0.3px;
    white-space: nowrap;
  }
  /* Back */
  .card-back { background: var(--card-blue); display: flex; }
  .back-logo-panel {
    width: 47%;
    background: var(--white);
    display: flex;
    align-items: center;
    justify-content: center;
    border-right: 3px solid var(--divider);
  }
  .back-logo-panel .brand { gap: 8px; }
  .back-logo-panel .brand-mark { width: 34px; height: 34px; background: var(--card-blue); }
  .back-logo-panel .brand-name { font-size: 28px; color: var(--card-blue); }
  .back-logo-panel .brand-tagline { font-size: 9px; color: var(--card-blue); margin-top: 3px; letter-spacing: 0.2px; }
  .contact-panel {
    flex: 1;
    padding: 52px 20px 0 34px;
    color: var(--white);
    font-family: "Roboto", sans-serif;
  }
  .holder-name { font-weight: 700; font-size: 23px; line-height: 1.1; white-space: nowrap; }
  .holder-title { font-size: 13px; margin-bottom: 18px; }
  .address { font-size: 13px; line-height: 1.35; margin-bottom: 14px; }
  .contact-list { list-style: none; font-size: 13px; line-height: 1.5; }
  .contact-list li { display: flex; align-items: center; gap: 8px; }
  .contact-list svg { width: 12px; height: 12px; flex: none; }
</style>
</head>
<body>
  <section class="card card-front" aria-label="Card front">
    <div class="brand">
      <span class="brand-mark"></span>
      <div class="brand-text">
        <span class="brand-name">Veltrano.co</span>
        <span class="brand-tagline">Polar Expeditions Specialists</span>
      </div>
    </div>
  </section>

  <section class="card card-back" aria-label="Card back">
    <div class="back-logo-panel">
      <div class="brand">
        <span class="brand-mark"></span>
        <div class="brand-text">
          <span class="brand-name">Veltrano.co</span>
          <span class="brand-tagline">Polar Expeditions Specialists</span>
        </div>
      </div>
    </div>
    <div class="contact-panel">
      <p class="holder-name">Marcus Lindqvist</p>
      <p class="holder-title">President</p>
      <p class="address">4120 Harbor View Road<br>Northgate, Canada 50218</p>
      <ul class="contact-list">
        <li>
          <svg viewBox="0 0 12 12" aria-hidden="true"><path d="M2.5 1l2 2.2-1 1.2a7 7 0 0 0 4.1 4.1l1.2-1L11 9.5 9.6 11C5 11 1 7 1 2.4z" fill="var(--white)"/></svg>
          555-210-4471
        </li>
        <li>
          <svg viewBox="0 0 12 12" aria-hidden="true"><rect x="3" y="0.8" width="6" height="10.4" rx="1" fill="none" stroke="var(--white)" stroke-width="1.2"/><circle cx="6" cy="9.3" r="0.7" fill="var(--white)"/></svg>
          555-318-9026
        </li>
        <li>
          <svg viewBox="0 0 12 12" aria-hidden="true"><rect x="0.8" y="2.3" width="10.4" height="7.4" fill="var(--white)"/><path d="M0.8 2.3L6 6.6l5.2-4.3" fill="none" stroke="var(--card-blue)" stroke-width="1"/></svg>
          info@veltrano.co
        </li>
        <li>
          <svg viewBox="0 0 12 12" aria-hidden="true"><circle cx="6" cy="6" r="5" fill="none" stroke="var(--white)" stroke-width="1.1"/><ellipse cx="6" cy="6" rx="2.2" ry="5" fill="none" stroke="var(--white)" stroke-width="1"/><path d="M1 6h10" stroke="var(--white)" stroke-width="1"/></svg>
          www.veltrano.co
        </li>
      </ul>
    </div>
  </section>
</body>
</html>
```